Velvet Dice Night Age Verification Landing Page

To create a visually appealing design for the landing page of the adult game "Velvet Dice Night" that confirms the visitor's age.
The design should have a simple and visually appealing look that focuses on two buttons labeled "Yes" and "No". The purpose of the page is to confirm that the visitor is 18 years of age or older before accessing the game's content. Responsive design that works well on desktop and mobile devices. The final output should be delivered in PSD, AI, or Sketch format, along with any necessary images or assets.
I have also attached examples.

```html
<!DOCTYPE html>
<html lang="en">
<head>
<meta charset="UTF-8">
<title>Velvet Dice Night – Age Verification</title>
<link href="https://fonts.googleapis.com/css2?family=Dancing+Script:wght@600;700&display=swap" rel="stylesheet">
<style>
  :root {
    --bg-deep: #2a1624;
    --bg-red: #6e1e2c;
    --bg-plum: #3a1f3a;
    --panel: rgba(48, 22, 44, 0.72);
    --panel-edge: rgba(120, 70, 110, 0.45);
    --accent: #94589e;
    --accent-light: #b57cc0;
    --text: #ffffff;
    --check: #d9c6dc;
  }
  * { margin: 0; padding: 0; box-sizing: border-box; }
  html, body { width: 1200px; height: 601px; overflow: hidden; }
  body {
    font-family: "Dancing Script", cursive;
    color: var(--text);
    position: relative;
  }
  .backdrop {
    position: absolute; inset: 0;
    background:
      radial-gradient(ellipse 35% 60% at 52% 55%, rgba(140, 40, 60, 0.55), transparent 70%),
      radial-gradient(ellipse 30% 45% at 15% 50%, rgba(110, 30, 45, 0.6), transparent 75%),
      linear-gradient(90deg, var(--bg-red) 0%, var(--bg-deep) 30%, #4a1a2c 55%, var(--bg-plum) 80%, #2b1a33 100%);
  }
  .age-gate {
    position: absolute;
    left: 350px; top: 141px;
    width: 486px; height: 302px;
    background: var(--panel);
    border: 1px solid var(--panel-edge);
    border-radius: 8px;
    box-shadow: 0 0 0 4px rgba(40, 18, 36, 0.35);
    text-align: center;
  }
  .brand-name {
    margin-top: 46px;
    font-size: 38px;
    font-weight: 700;
    color: var(--accent-light);
    line-height: 1;
  }
  .question {
    margin-top: 40px;
    font-size: 23px;
    font-weight: 600;
  }
  .choices {
    display: flex; justify-content: center; gap: 8px;
    margin-top: 16px;
  }
  .choice {
    width: 125px; height: 39px;
    border-radius: 20px;
    background: var(--accent);
    color: var(--text);
    font-family: "Dancing Script", cursive;
    font-size: 24px; font-weight: 600;
    border: none;
  }
  .remember {
    display: inline-flex; align-items: center; gap: 9px;
    margin-top: 22px;
    font-size: 16px; font-weight: 600;
  }
  .remember-box {
    width: 15px; height: 15px;
    border-radius: 4px;
    background: var(--check);
    border: 2px solid var(--accent);
  }
</style>
</head>
<body>
  <div class="backdrop" role="img" aria-label="Moody dark red boudoir photograph of a woman in lace lingerie, blurred behind the age prompt"></div>
  <main class="age-gate">
    <div class="brand-name">Velvet Dice Night</div>
    <h1 class="question">Are you over 18 years of age?</h1>
    <div class="choices">
      <button class="choice">Yes</button>
      <button class="choice">No</button>
    </div>
    <label class="remember"><span class="remember-box"></span>Remember me</label>
  </main>
</body>
</html>
```